Navoro & Omvar Automotive Repair Shop. Need a new website design.

We specialize in Navoro & Omvar auto repair, but also work on other Asian import vehicles. We have been in business for 7 years and pride ourselves on high quality auto repair that is fixed right the first time. Would like the automotive repair website to incorporate the colors black, red and white if possible and have our logo and some Navoro and Omvar vehicles included in the website.

Target Market(s)

Navoro & Omvar vehicle owners

Industry/Entity Type

Automotive Repair

Coding

Coded - Design and coding required

Number of Pages Required

5+ page

Colors
EB3D1F
EC4F4E
F09395
F8D3D4
FCEDEE

Requirements
Must have
• Home, Services, Contact Us, Schedule appointment, and a gallery tab that I can add shop pictures to when completed.
Nice to have
• Would like to see example pictures of job next to each service listed.
Should not have
• Service not related to auto repair. Ex. auto detailing, towing, car wash

```html
<!DOCTYPE html>
<html lang="en">
<head>
<meta charset="utf-8">
<title>Varden Automotive – Navoro &amp; Omvar Auto Repair</title>
<link rel="stylesheet" href="https://fonts.googleapis.com/css2?family=Barlow:wght@400;500;600;700&family=Krona+One&display=swap">
<style>
:root{
  --red:#e21b1b;
  --red-deep:#b50d0f;
  --black:#0e0e0e;
  --dark:#1a1a1a;
  --panel:#151515;
  --white:#ffffff;
  --text:#2a2a2a;
  --display:"Krona One",sans-serif;
  --body:"Barlow",sans-serif;
}
*{box-sizing:border-box;margin:0;padding:0}
html,body{width:1200px;height:4612px;overflow:hidden;background:var(--white)}
body{position:relative;font-family:var(--body);color:var(--text)}
.abs{position:absolute}
.display{font-family:var(--display);text-transform:uppercase;letter-spacing:1px}
.eyebrow{font-family:var(--display);color:var(--red);font-size:14px;letter-spacing:1px;text-transform:uppercase}
.btn{position:absolute;display:flex;align-items:center;justify-content:center;font-family:var(--body);font-weight:700;text-transform:uppercase;font-size:15px;letter-spacing:.5px}
.btn-red{background:var(--red);color:var(--white)}

/* hero */
.hero{left:0;top:0;width:1200px;height:800px;background:linear-gradient(180deg,#0c0c0c,#1c1c1c)}
.hero-photo{right:0;top:0;width:720px;height:780px;
  background:
    radial-gradient(ellipse 180px 120px at 82% 36%,rgba(190,140,110,.55),rgba(190,140,110,0) 70%),
    radial-gradient(ellipse 260px 200px at 58% 58%,#d8d8d8 0%,rgba(216,216,216,0) 70%),
    radial-gradient(ellipse 220px 160px at 70% 22%,#bdbdbd 0%,rgba(189,189,189,0) 75%),
    radial-gradient(ellipse at 62% 48%,#8d8d8d 0%,#4b4b4b 40%,#1e1e1e 72%,#111 100%)}
.logo{left:135px;top:50px;height:70px;display:flex;align-items:center;gap:10px;color:var(--white);font-family:var(--body);font-weight:700;font-size:30px;letter-spacing:1px}
.logo .mark{width:20px;height:20px;background:var(--red)}
.nav{top:48px;left:367px;font-size:13px;font-weight:500;color:var(--white);text-transform:uppercase}
.nav a{position:absolute;white-space:nowrap;color:var(--white);text-decoration:none}
.nav a.active::after{content:"";position:absolute;left:0;right:0;bottom:-12px;height:2px;background:var(--red)}
.finance-btn{left:922px;top:45px;width:183px;height:34px;border:1px solid var(--white);color:var(--white);font-size:12px;border-radius:2px}
.hero-frame{left:125px;top:247px;width:300px;height:365px;border:4px solid #cfcfcf;border-right:none}
.hero-title{left:172px;top:290px;font-size:29px;line-height:41px;color:var(--white)}
.hero-title .red{color:var(--red)}
.hero-copy{left:172px;top:420px;width:390px;font-size:15px;line-height:21px;color:#e8e8e8}
.hero-cta{left:172px;top:505px;width:281px;height:53px}

/* about */
.about-photo{left:112px;top:852px;width:346px;height:418px;
  background:
    radial-gradient(ellipse 90px 70px at 58% 36%,#2b2b2b,rgba(43,43,43,0) 80%),
    linear-gradient(100deg,rgba(0,0,0,0) 0%,rgba(0,0,0,0) 55%,rgba(214,170,40,.65) 56%,rgba(214,170,40,.65) 62%,rgba(0,0,0,0) 63%),
    radial-gradient(ellipse 120px 120px at 55% 85%,#2a3240,rgba(42,50,64,0) 80%),
    linear-gradient(170deg,#a09a90,#6a6660 45%,#3a3835)}
.about-accent{left:104px;top:842px;width:60px;height:40px;background:var(--red)}
.about-engine{left:58px;top:1115px;width:205px;height:200px;border-radius:30% 30% 40% 40%;
  background:radial-gradient(ellipse at 45% 40%,#fafafa 0%,#cfcfcf 30%,#8c8c8c 60%,#4a4a4a 85%,#2e2e2e 100%)}
.years{left:458px;top:1164px;width:124px;height:113px;background:var(--red);color:var(--white);text-align:center;padding-top:14px}
.years b{display:block;font-family:var(--display);font-size:34px;line-height:40px}
.years span{display:block;font-size:14px;font-weight:600;line-height:17px;text-transform:uppercase}
.about-eyebrow{left:609px;top:855px}
.about-title{left:609px;top:878px;font-size:31px;color:#1a1a1a}
.about-rule{left:985px;top:893px;width:215px;height:2px;background:var(--red)}
.about-rule::before{content:"";position:absolute;left:0;top:-4px;width:10px;height:10px;background:var(--red)}
.about-lead{left:612px;top:933px;width:520px;font-size:15.5px;line-height:23px;font-weight:600;color:#1d1d1d}
.about-body{left:612px;top:1020px;width:520px;font-size:14px;line-height:21.6px;color:#444}
.learn-btn{left:618px;top:1229px;width:166px;height:46px;border:2px solid var(--red);color:var(--red);font-size:14px;letter-spacing:1.5px}

/* partners */
.services-bg{left:0;top:1540px;width:1200px;height:720px;background:linear-gradient(180deg,#1d1d1d,#121212)}
.partner-box{left:111px;top:1361px;width:958px;height:256px;background:var(--panel);border:1px solid #333}
.partner-corner-a{left:105px;top:1356px;width:92px;height:12px;background:#444}
.partner-corner-b{left:1020px;top:1560px;width:55px;height:62px;border-right:5px solid #555;border-bottom:5px solid #555}
.partner-title{left:0;width:1200px;top:1410px;text-align:center;color:var(--white);font-size:16px;line-height:24px}
.badge-square{left:233px;top:1462px;width:82px;height:110px;background:#f2f2f2;border-radius:4px;padding:10px}
.badge-square::before{content:"";display:block;width:62px;height:52px;background:#1d4fa0;border-radius:4px}
.badge-laurel{left:412px;top:1468px;width:106px;height:106px;border-radius:50%;border:4px solid #2d8c9e;background:#141e22}
.partner-plate{top:1480px;height:80px;display:flex;align-items:center;justify-content:center;color:var(--red);font-family:var(--body);font-weight:700;font-size:26px;white-space:nowrap}
.partner-plate.light{background:#f1f1f1;border-radius:4px}

/* services */
.services-eyebrow{left:0;width:1200px;top:1684px;text-align:center}
.services-title{left:0;width:1200px;top:1708px;text-align:center;color:var(--white);font-size:29px}
.svc-active{left:97px;top:1788px;width:284px;height:50px;background:var(--red);clip-path:polygon(0 0,100% 0,93% 100%,0 100%)}
.svc{position:absolute;display:flex;align-items:flex-start;gap:14px;color:var(--white);font-size:15.5px;line-height:23px;width:340px}
.svc svg{flex:none;width:30px;height:30px;margin-top:-4px}

/* gallery */
.gallery-bg{left:0;top:2221px;width:1200px;height:880px;background:linear-gradient(180deg,#cfcfcf 0%,#f1f1f1 45%,#d6d6d6 100%)}
.gallery-eyebrow{left:0;width:1200px;top:2415px;text-align:center}
.gallery-title{left:0;width:1200px;top:2440px;text-align:center;font-size:30px;color:#1a1a1a}

/* makes */
.makes{left:0;top:3090px;width:1200px;height:662px;background:var(--black)}
.makes-title{left:0;width:1200px;top:3160px;text-align:center;color:var(--white);font-size:20px;line-height:25px}
.make-grid{left:131px;top:3283px;width:919px;height:286px;display:grid;grid-template-columns:repeat(4,1fr);grid-template-rows:repeat(2,1fr);border:1px solid #555}
.make{border:1px solid #555;display:flex;align-items:center;justify-content:center;gap:10px;color:var(--white);font-weight:700;font-size:24px;letter-spacing:2px;text-transform:uppercase}
.make i{width:14px;height:14px;border:2px solid currentColor;border-radius:50%}
.make.hover{background:linear-gradient(135deg,#f4f4f4,#b9b9b9);color:#222}
.makes-cta{left:453px;top:3616px;width:290px;height:56px;font-size:16px;background:linear-gradient(90deg,var(--red),var(--red-deep))}

/* contact */
.contact{left:0;top:3752px;width:1200px;height:555px;background:
  radial-gradient(ellipse 420px 200px at 28% 78%,rgba(120,6,8,.5),rgba(120,6,8,0) 75%),
  linear-gradient(135deg,#d71414 0%,#b80d0f 55%,#8e0a0b 100%)}
.contact-eyebrow{left:135px;top:3896px;color:#fff;font-size:14px}
.contact-line{left:0;top:3947px;width:112px;height:2px;background:#fff}
.contact-line::after{content:"";position:absolute;right:-4px;top:-3px;width:8px;height:8px;background:#fff}
.contact-title{left:135px;top:3920px;color:#fff;font-size:30px}
.contact-copy{left:135px;top:3990px;width:400px;color:#fff;font-size:15px;line-height:27px}
.contact-btn{left:140px;top:4087px;width:234px;height:43px;border:2px solid #fff;color:#fff;font-size:13px}
.form-card{left:595px;top:3827px;width:490px;height:364px;background:linear-gradient(180deg,#f3f3f3,#dcdcdc);border-radius:6px}
.form-title{left:637px;top:3870px;font-size:16px;color:#222}
.field{position:absolute;border:1px solid #b5b5b5;background:#f7f7f7;font-size:10.5px;color:#333;padding:8px 14px}
.submit{left:638px;top:4114px;width:132px;height:34px;font-size:13px;font-family:var(--display)}

/* footer */
.footer{left:0;top:4307px;width:1200px;height:305px;background:var(--dark)}
.footer-logo{left:540px;top:4350px}
.footer-nav{top:4450px;color:#fff;font-weight:700;font-size:16px;text-transform:uppercase;white-space:nowrap}
.footer-dot{top:4458px;width:6px;height:6px;background:var(--red)}
.copyright{left:168px;top:4511px;font-size:12px;color:#ddd}
.social{top:4542px;font-size:13px;color:#fff;font-weight:600}
.payvia{left:856px;top:4522px;display:flex;align-items:center;gap:10px;color:#2bd18a;font-weight:700;font-size:28px}
.payvia i{width:22px;height:22px;border-radius:50%;background:#2bd18a}
.payvia small{font-size:13px;font-weight:500;align-self:flex-end;margin-bottom:4px}
</style>
</head>
<body>

<!-- HERO -->
<section class="abs hero">
  <div class="abs hero-photo" role="img" aria-label="Mechanic's hands working on an exposed engine cylinder head"></div>
  <div class="abs" style="left:0;top:0;width:720px;height:800px;background:linear-gradient(90deg,#111 62%,rgba(17,17,17,0))"></div>
  <svg class="abs" style="left:0;top:660px" width="1200" height="140" viewBox="0 0 1200 140" aria-hidden="true">
    <polygon points="0,118 600,20 1200,118 1200,140 0,140" fill="var(--red)"/>
    <polygon points="0,140 0,130 600,48 1200,130 1200,140" fill="#ffffff"/>
  </svg>
  <div class="abs logo"><span class="mark"></span>VARDEN</div>
  <nav class="abs nav">
    <a class="active" style="left:0">Home</a>
    <a style="left:84px">About Us</a>
    <a style="left:193px">Our Services</a>
    <a style="left:348px">Gallery</a>
    <a style="left:455px">Contact</a>
  </nav>
  <div class="btn finance-btn">Financing Application</div>
  <div class="abs hero-frame"></div>
  <h1 class="abs display hero-title">Specializing in<br>Navoro and Omvar<br><span class="red">Auto Repair</span></h1>
  <p class="abs hero-copy">Varden Automotive is a locally owned and operated auto repair shop in Millbrook that offers comprehensive car care and services</p>
  <div class="btn btn-red hero-cta">Schedule an Appointment</div>
</section>

<!-- ABOUT -->
<section>
  <div class="abs about-accent"></div>
  <div class="abs about-photo" role="img" aria-label="Technician working underneath a lifted vehicle"></div>
  <div class="abs about-engine" role="img" aria-label="Chrome engine block rendering"></div>
  <div class="abs years"><b>20</b><span>Years of<br>Experience</span></div>
  <div class="abs eyebrow about-eyebrow">Our Company</div>
  <h2 class="abs display about-title">About Varden</h2>
  <div class="abs about-rule"></div>
  <p class="abs about-lead">Varden Automotive is a locally owned and operated auto repair shop in Millbrook that offers comprehensive car care and services for Navoro &amp; Omvar and all other Asian imports vehicles.</p>
  <p class="abs about-body">Led by a CMT master certified technician with 20 years experience working for Navoro &amp; Omvar dealerships, our auto shop is your go to facility for everything from factory auto maintenance, including oil changes, fluid services and tune ups, to complex engine repairs, hybrid diagnostic &amp; repair, brake jobs, etc. We have state of the art equipment and tools to ensure that we can properly diagnose and repair your vehicle to get you back on the road quickly. Our work comes with a warranty and we offer towing if needed. We also offer discounts for Rydo &amp; Glide rides.</p>
  <div class="btn learn-btn">Learn More</div>
</section>

<!-- PARTNERS + SERVICES -->
<section>
  <div class="abs services-bg"></div>
  <div class="abs partner-corner-a"></div>
  <div class="abs partner-corner-b"></div>
  <div class="abs partner-box"></div>
  <h3 class="abs display partner-title">Authorized installer for Korvane oil,<br>Tristar Battery</h3>
  <div class="abs badge-square"></div>
  <div class="abs badge-laurel"></div>
  <div class="abs partner-plate light" style="left:600px;width:150px">TRISTAR</div>
  <div class="abs partner-plate" style="left:820px;width:175px">KORVANE</div>

  <div class="abs eyebrow services-eyebrow">What We Do</div>
  <h2 class="abs display services-title">Services Provide</h2>
  <div class="abs svc-active"></div>

  <!-- column 1 -->
  <div class="svc" style="left:122px;top:1804px"><svg viewBox="0 0 30 30"><circle cx="15" cy="15" r="11" fill="none" stroke="#fff" stroke-width="1.6"/><path d="M10 15h10M15 10v10" stroke="#fff" stroke-width="1.6"/></svg>Oil Changes</div>
  <div class="svc" style="left:122px;top:1851px"><svg viewBox="0 0 30 30"><rect x="5" y="6" width="20" height="15" fill="none" stroke="#fff" stroke-width="1.6"/><path d="M11 25h8" stroke="#fff" stroke-width="1.6"/></svg>Computer Diagnostics</div>
  <div class="svc" style="left:122px;top:1897px"><svg viewBox="0 0 30 30"><circle cx="15" cy="15" r="11" fill="none" stroke="#fff" stroke-width="1.6"/><path d="M16 8l-5 8h5l-2 7 6-9h-5z" fill="#fff"/></svg>Electrical Specialists</div>
  <div class="svc" style="left:122px;top:1944px"><svg viewBox="0 0 30 30"><circle cx="15" cy="15" r="11" fill="none" stroke="#fff" stroke-width="1.6"/><circle cx="15" cy="15" r="5" fill="none" stroke="#fff" stroke-width="1.6"/></svg>Tires</div>
  <div class="svc" style="left:122px;top:1990px"><svg viewBox="0 0 30 30"><circle cx="13" cy="17" r="8" fill="none" stroke="#fff" stroke-width="1.6"/><path d="M20 5l5 5" stroke="#fff" stroke-width="1.6"/></svg>Tire Balance &amp; Rotations</div>
  <div class="svc" style="left:122px;top:2037px"><svg viewBox="0 0 30 30"><circle cx="13" cy="13" r="8" fill="none" stroke="#fff" stroke-width="1.6"/><path d="M19 19l7 7" stroke="#fff" stroke-width="1.6"/></svg>Pre Purchase Inspections</div>
  <div class="svc" style="left:122px;top:2082px"><svg viewBox="0 0 30 30"><rect x="4" y="12" width="22" height="8" rx="3" fill="none" stroke="#fff" stroke-width="1.6"/><circle cx="9" cy="21" r="2.5" fill="#fff"/><circle cx="21" cy="21" r="2.5" fill="#fff"/></svg>Insurance Claims</div>
  <div class="svc" style="left:122px;top:2128px"><svg viewBox="0 0 30 30"><rect x="4" y="11" width="22" height="10" fill="none" stroke="#fff" stroke-width="1.6"/><path d="M9 5v4M13 5v4M17 5v4" stroke="#fff" stroke-width="1.6"/></svg>Emission Repair &amp; Catalytic<br>Converters</div>

  <!-- column 2 -->
  <div class="svc" style="left:426px;top:1804px"><svg viewBox="0 0 30 30"><rect x="6" y="8" width="18" height="14" fill="none" stroke="#fff" stroke-width="1.6"/><path d="M10 8V5h10v3" stroke="#fff" stroke-width="1.6"/></svg>Engine Repair</div>
  <div class="svc" style="left:426px;top:1851px"><svg viewBox="0 0 30 30"><rect x="5" y="6" width="20" height="18" fill="none" stroke="#fff" stroke-width="1.6"/><path d="M9 10v10M13 10v10M17 10v10M21 10v10" stroke="#fff" stroke-width="1.2"/></svg>Heating &amp; AC Repair</div>
  <div class="svc" style="left:426px;top:1897px"><svg viewBox="0 0 30 30"><path d="M5 20l3-8h14l3 8z" fill="none" stroke="#fff" stroke-width="1.6"/><circle cx="10" cy="22" r="2.5" fill="#fff"/><circle cx="20" cy="22" r="2.5" fill="#fff"/></svg>State Inspection</div>
  <div class="svc" style="left:426px;top:1944px"><svg viewBox="0 0 30 30"><path d="M15 4v22M10 8h10M10 14h10M10 20h10" stroke="#fff" stroke-width="1.6"/></svg>Suspension Service &amp; Repair</div>
  <div class="svc" style="left:426px;top:1990px"><svg viewBox="0 0 30 30"><path d="M6 24L24 6M8 6l16 18" stroke="#fff" stroke-width="1.6"/></svg>Leveling Kits &amp; Minor Lift Kit installation</div>
  <div class="svc" style="left:426px;top:2037px"><svg viewBox="0 0 30 30"><circle cx="15" cy="15" r="11" fill="none" stroke="#fff" stroke-width="1.6"/><circle cx="15" cy="15" r="3" fill="#fff"/></svg>Brakes Service &amp; Repair</div>
  <div class="svc" style="left:426px;top:2082px"><svg viewBox="0 0 30 30"><path d="M5 25L22 8l3 3L8 28z" fill="none" stroke="#fff" stroke-width="1.6"/></svg>Exhaust, Muffler Service &amp; Repair</div>
  <div class="svc" style="left:426px;top:2128px"><svg viewBox="0 0 30 30"><path d="M8 5v20M15 5v20M22 5v10M8 15h14" stroke="#fff" stroke-width="1.6"/></svg>Automatic, Manual, Computerized<br>Transmission Service &amp; Repair</div>

  <!-- column 3 -->
  <div class="svc" style="left:788px;top:1804px"><svg viewBox="0 0 30 30"><rect x="6" y="7" width="18" height="16" fill="none" stroke="#fff" stroke-width="1.6"/><path d="M6 15h18" stroke="#fff" stroke-width="1.6"/></svg>Clutch Service &amp; Repair</div>
  <div class="svc" style="left:788px;top:1851px"><svg viewBox="0 0 30 30"><rect x="3" y="10" width="7" height="10" fill="none" stroke="#fff" stroke-width="1.6"/><rect x="20" y="10" width="7" height="10" fill="none" stroke="#fff" stroke-width="1.6"/><path d="M10 15h10" stroke="#fff" stroke-width="1.6"/></svg>CV Axle Service &amp; Repair</div>
  <div class="svc" style="left:788px;top:1897px"><svg viewBox="0 0 30 30"><path d="M15 4c5 7 8 11 8 15a8 8 0 0 1-16 0c0-4 3-8 8-15z" fill="none" stroke="#fff" stroke-width="1.6"/></svg>Fuel Injection System Service<br>Cleaning &amp; Repair</div>
  <div class="svc" style="left:788px;top:1965px"><svg viewBox="0 0 30 30"><circle cx="12" cy="15" r="8" fill="none" stroke="#fff" stroke-width="1.6"/><circle cx="22" cy="9" r="4" fill="none" stroke="#fff" stroke-width="1.6"/></svg>Timing Belts &amp; Water Pumps</div>
  <div class="svc" style="left:788px;top:2012px"><svg viewBox="0 0 30 30"><rect x="5" y="6" width="20" height="18" fill="none" stroke="#fff" stroke-width="1.6"/><path d="M10 6v18M15 6v18M20 6v18" stroke="#fff" stroke-width="1.2"/></svg>Radiators &amp; Fans Service &amp; Repair</div>
  <div class="svc" style="left:788px;top:2058px"><svg viewBox="0 0 30 30"><rect x="6" y="8" width="18" height="14" fill="none" stroke="#fff" stroke-width="1.6"/><path d="M11 8V4M19 8V4" stroke="#fff" stroke-width="1.6"/></svg>Tune ups &amp; Factory Scheduled<br>Maintenance</div>
  <div class="svc" style="left:788px;top:2128px"><svg viewBox="0 0 30 30"><circle cx="15" cy="15" r="11" fill="none" stroke="#fff" stroke-width="1.6"/><path d="M16 8l-5 8h5l-2 7 6-9h-5z" fill="none" stroke="#fff" stroke-width="1.2"/></svg>Hybrid Vehicle diagnostic &amp; repair<br>24-hr Night Drop</div>
</section>

<!-- GALLERY -->
<section>
  <div class="abs gallery-bg"></div>
  <svg class="abs" style="left:0;top:2215px" width="1200" height="120" viewBox="0 0 1200 120" aria-hidden="true">
    <polygon points="0,0 1200,0 1200,12 600,110 0,12" fill="#161616"/>
    <polygon points="0,12 600,110 1200,12 1200,26 600,120 0,26" fill="#9c9c9c" opacity=".6"/>
  </svg>
  <div class="abs eyebrow gallery-eyebrow">Photo Gallery</div>
  <h2 class="abs display gallery-title">Our Gallery</h2>
  <div class="abs" style="left:107px;top:2513px;width:323px;height:238px;background:radial-gradient(ellipse 90px 60px at 35% 70%,rgba(200,150,60,.55),rgba(200,150,60,0) 80%),linear-gradient(160deg,#8a8780,#4d4a46 50%,#2a2826)" role="img" aria-label="Technician repairing a vehicle suspension"></div>
  <div class="abs" style="left:442px;top:2513px;width:323px;height:238px;background:radial-gradient(ellipse 60px 40px at 45% 60%,rgba(220,40,40,.6),rgba(220,40,40,0) 80%),radial-gradient(ellipse 160px 90px at 50% 35%,#b8b8b8,rgba(184,184,184,0) 80%),linear-gradient(180deg,#6c6c6c,#2c2c2c 70%,#1b1b1b)" role="img" aria-label="Luxury SUV with hood open in the shop"></div>
  <div class="abs" style="left:777px;top:2513px;width:323px;height:238px;background:radial-gradient(ellipse 120px 80px at 30% 20%,rgba(40,80,170,.7),rgba(40,80,170,0) 80%),radial-gradient(ellipse 140px 90px at 55% 60%,#8a8a8a,rgba(138,138,138,0) 80%),linear-gradient(170deg,#3b4252,#2a2a2a)" role="img" aria-label="Engine bay during a major repair"></div>
  <div class="abs" style="left:111px;top:2769px;width:487px;height:236px;background:linear-gradient(90deg,rgba(0,0,0,0) 0%,rgba(0,0,0,0) 51%,rgba(40,80,200,.8) 52%,rgba(40,80,200,.8) 56%,rgba(0,0,0,0) 57%),radial-gradient(ellipse 200px 80px at 45% 40%,#d8d8d8,rgba(216,216,216,0) 80%),linear-gradient(180deg,#8c8c8c,#5a5a5a 60%,#3c3c3c)" role="img" aria-label="Pickup truck raised on a blue lift"></div>
  <div class="abs" style="left:612px;top:2769px;width:488px;height:236px;background:linear-gradient(180deg,#b9b3a6 0%,#a39c8e 45%,#2f2f31 60%,#3c3c3e 78%,#7f7c78 100%)" role="img" aria-label="Row of SUVs parked in front of the shop"></div>
</section>

<!-- MAKES -->
<section>
  <div class="abs makes"></div>
  <h2 class="abs display makes-title">Varden Automotive specializes in Navoro &amp; Omvar<br>auto repair but also service and repair<br>the following makes</h2>
  <div class="abs make-grid">
    <div class="make"><i></i>Alvera</div>
    <div class="make"><i></i>Hanvio</div>
    <div class="make"><i></i>Infera</div>
    <div class="make"><i></i>Kesta</div>
    <div class="make hover"><i></i>Mirado</div>
    <div class="make"><i></i>Mazuro</div>
    <div class="make"><i></i>Nisora</div>
    <div class="make"><i></i>Hoveno</div>
  </div>
  <div class="btn btn-red makes-cta">Financing Application</div>
</section>

<!-- CONTACT -->
<section>
  <div class="abs contact"></div>
  <div class="abs eyebrow contact-eyebrow">Get in Touch</div>
  <h2 class="abs display contact-title">Contact Us</h2>
  <div class="abs contact-line"></div>
  <p class="abs contact-copy">Contact us for a free estimate! Please include year, make, and model and the service or repair you would like repair you would like an estimate on.</p>
  <div class="btn contact-btn">Schedule an Appointment</div>

  <div class="abs form-card"></div>
  <h3 class="abs display form-title">Leave us a message</h3>
  <div class="field" style="left:636px;top:3915px;width:200px;height:38px">First Name*</div>
  <div class="field" style="left:848px;top:3915px;width:200px;height:38px">Last Name*</div>
  <div class="field" style="left:636px;top:3965px;width:200px;height:38px">Email address*</div>
  <div class="field" style="left:848px;top:3965px;width:200px;height:38px">Phone*</div>
  <div class="field" style="left:636px;top:4013px;width:412px;height:83px">Message</div>
  <div class="btn btn-red submit">Submit</div>
</section>

<!-- FOOTER -->
<footer>
  <div class="abs footer"></div>
  <svg class="abs" style="left:0;top:4290px" width="1200" height="80" viewBox="0 0 1200 80" aria-hidden="true">
    <polygon points="0,17 540,17 600,0 660,17 1200,17 1200,34 680,34 600,70 520,34 0,34" fill="var(--red)"/>
    <polygon points="0,34 520,34 600,70 680,34 1200,34 1200,80 0,80" fill="var(--dark)"/>
  </svg>
  <div class="abs logo footer-logo"><span class="mark"></span>VARDEN</div>
  <div class="abs footer-nav" style="left:170px">Home</div>
  <div class="abs footer-dot" style="left:276px"></div>
  <div class="abs footer-nav" style="left:330px">About Us</div>
  <div class="abs footer-dot" style="left:468px"></div>
  <div class="abs footer-nav" style="left:520px">Our Services</div>
  <div class="abs footer-dot" style="left:694px"></div>
  <div class="abs footer-nav" style="left:748px">Gallery</div>
  <div class="abs footer-dot" style="left:872px"></div>
  <div class="abs footer-nav" style="left:933px">Contact</div>
  <p class="abs copyright">Copyright © 2024 Varden Automotive. All rights reserved.</p>
  <div class="abs social" style="left:168px">Friendly</div>
  <div class="abs social" style="left:232px">Chirp</div>
  <div class="abs social" style="left:280px">Linkup</div>
  <div class="abs social" style="left:334px">Snapgram</div>
  <div class="abs payvia"><i></i>Payvia<small>finance</small></div>
</footer>

</body>
</html>
```